Luxury Business Card Design for High-End Window Treatments

Gilded Slatworks
Custom Plantation Shutters & Architectural Shading Systems

⸻

BACK

Daniel Trevick
Owner

Custom Interior & Exterior Window Treatments

919-555-0148
gildedslatworks.com

I have included a picture that I’m hoping we can use on the back, but I’m also wondering if you can get rid of the ladder? Should we get rid of shutters , shades and blinds underneath Gilded Slatworks?

Target Market(s)

High-end residential homeowners, custom home builders, architects, interior designers, and luxury renovation clients seeking premium plantation shutters and motorized architectural shading systems.

Industry/Entity Type

Custom Window treatments

Contact Information for Business Card

Front Gilded Slatworks Custom Plantation Shutters Motorized Architectural Shading Systems BACK Daniel Trevick Owner 919-555-0148 GildedSlatworks.com Custom Interior & Exterior Window Treatments By Appointment

Requirements
Nice to have
• Not 100% sure on nice to halves or the color but you can definitely check out my website to get a better understanding of what I’m trying to do

```html
<!DOCTYPE html>
<html lang="en">
<head>
<meta charset="utf-8">
<title>Gilded Slatworks – Business Cards</title>
<link rel="stylesheet" href="https://fonts.googleapis.com/css2?family=Montserrat:wght@400;600;700&family=Roboto+Slab:wght@600&display=swap">
<style>
  :root {
    --bg: #b9b9b9;
    --card: #050607;
    --gold: #d8bd58;
    --gold-edge: #c9b04a;
    --white: #f4f4f2;
    --muted: #c9c9c4;
    --sky: #6e9fd6;
    --house: #5c6a58;
  }
  html, body {
    margin: 0;
    width: 1200px;
    height: 815px;
    overflow: hidden;
    background: var(--bg);
  }
  .canvas {
    position: relative;
    width: 1200px;
    height: 815px;
  }
  .card {
    position: absolute;
    background: var(--card);
    border: 4px solid var(--gold-edge);
    border-radius: 28px;
    overflow: hidden;
    box-sizing: border-box;
  }
  .card-contact {
    left: 70px;
    top: 92px;
    width: 360px;
    height: 630px;
  }
  .card-brand {
    left: 500px;
    top: 227px;
    width: 630px;
    height: 360px;
    display: flex;
    align-items: center;
    justify-content: center;
  }
  .house-photo {
    height: 270px;
    background: linear-gradient(180deg, var(--sky) 0%, #8fb4df 35%, #9a9a88 60%, var(--house) 100%);
  }
  .contact-body {
    padding: 26px 30px 0 40px;
  }
  .brand {
    font-family: "Roboto Slab", Georgia, serif;
    color: var(--gold);
    text-align: left;
  }
  .brand-name {
    font-weight: 600;
    font-size: 30px;
    line-height: 1.05;
    margin: 0;
  }
  .brand-tagline {
    font-weight: 600;
    font-size: 14px;
    letter-spacing: 0.5px;
    margin: 8px 0 0;
    word-spacing: 10px;
  }
  .card-brand .brand { text-align: center; }
  .card-brand .brand-name { font-size: 62px; }
  .card-brand .brand-tagline { font-size: 24px; margin-top: 16px; word-spacing: 18px; }
  .brand-subline {
    font-family: "Montserrat", Arial, sans-serif;
    font-weight: 400;
    font-size: 13px;
    letter-spacing: 1.5px;
    color: var(--muted);
    margin: 14px 0 0;
  }
  .person { margin-top: 20px; font-family: "Montserrat", Arial, sans-serif; }
  .person-name { color: var(--gold); font-weight: 700; font-size: 24px; margin: 0; }
  .person-role { color: var(--white); font-size: 14px; margin: 2px 0 0; }
  .person-service { color: var(--muted); font-size: 12px; margin: 6px 0 0; }
  .contact-list {
    list-style: none;
    padding: 0;
    margin: 16px 0 0;
    font-family: "Montserrat", Arial, sans-serif;
    font-size: 14px;
    color: var(--white);
  }
  .contact-list li { display: flex; align-items: center; gap: 10px; margin-bottom: 7px; }
  .contact-list svg { width: 14px; height: 14px; flex: none; }
  .web-domain { color: var(--gold); }
  .appointment {
    margin: 8px 0 0;
    font-family: "Montserrat", Arial, sans-serif;
    font-weight: 600;
    font-size: 11px;
    letter-spacing: 2px;
    text-transform: uppercase;
    color: var(--gold);
  }
</style>
</head>
<body>
<main class="canvas">
  <section class="card card-contact">
    <div class="house-photo" role="img" aria-label="Photo of a two-storey house with screened porches under a blue sky"></div>
    <div class="contact-body">
      <div class="brand">
        <p class="brand-name">Gilded<br>Slatworks</p>
        <p class="brand-tagline">Shutters Shades Blinds</p>
      </div>
      <div class="person">
        <p class="person-name">Daniel Trevick</p>
        <p class="person-role">Owner</p>
        <p class="person-service">Custom Interior &amp; Exterior Window Treatments</p>
      </div>
      <ul class="contact-list">
        <li>
          <svg viewBox="0 0 14 14"><rect x="3.5" y="1" width="7" height="12" rx="1.5" fill="none" stroke="var(--gold)" stroke-width="1.4"/></svg>
          919-555-0148
        </li>
        <li>
          <svg viewBox="0 0 14 14"><rect x="1" y="3" width="12" height="8" fill="var(--gold)"/><path d="M1 3l6 5 6-5" fill="none" stroke="var(--card)" stroke-width="1.2"/></svg>
          info@gildedslatworks.com
        </li>
        <li>
          <svg viewBox="0 0 14 14"><circle cx="7" cy="7" r="6" fill="var(--gold)"/><path d="M1 7h12M7 1v12M3 3.5h8M3 10.5h8" stroke="var(--card)" stroke-width="0.9" fill="none"/></svg>
          <span>www.<span class="web-domain">gildedslatworks.com</span></span>
        </li>
      </ul>
      <p class="appointment">By Appointment</p>
    </div>
  </section>

  <section class="card card-brand">
    <div class="brand">
      <p class="brand-name">Gilded<br>Slatworks</p>
      <p class="brand-tagline">Shutters Shades Blinds</p>
      <p class="brand-subline">Custom Plantation Shutters · Architectural Shading Systems</p>
    </div>
  </section>
</main>
</body>
</html>
```